Business Name: DM Space Arranging Pty Ltd

Business Type: Professional Home Styling and Minor Renovation Business

Logo: Attached is the logo that has been created.
I always envisaged the logo in the middle of the business card with my full name underneath it.

Marnie Tulloch B.Com LMR HTV
Property Stylist & Project Manager

Include dot points of services
Staging Houses for Sale
Minor Home Renovations
Home Styling & Project Management
Re-Designing Living Spaces to Aid the Disabled

Somewhere on the card I would like to incorporate
"Property Styling and Cosmetic Renovations"

Colour Scheme:
Gloss black business card, with white and then
Gold or Silver as the highlight colours.

Incorporate a small amount of yellow only if possible to make it pop. If this really doesn’t work it doesn’t have to be used. Also l like the colour teal if that needs to be used as a contrast colour.

Feel/Themes
• I love antique chairs, regal expensive looking furniture mixed with modern homes (this is the unique style I want to sell) antique and modern mix that looks high class as well as modern and fresh, targeting an executive market.
• I want to use an orchid as a trademark throughout the course of my work, not sure if this can somehow be incorporated? Also really like crowns to give that regal/antique feel and then something else to give that modern twist (I don’t know what the something else could be)
• Wall Paper Look (on a portion of it not all of it, like a French look)
• Overall feel - A very deluxe and professional feel with a little bit of creative flare.

I hope this helps create a bit of a picture.

Is it ok that I call you tomorrow morning? My mobile number is 0438 926 574 if you have any questions for me in the meantime.

Target Market(s)

High Quality Executive Market - People selling homes

Industry/Entity Type

Business

Contact Information for Business Card

Include dot points of services:
Staging Houses for Sale
Minor Home Renovations

Font styles to use
Serif
Script

Colors
33b8a4
fbed22

Requirements
Must have
• Marnie Tulloch B.Com LMR HTV
• Property Stylist & Project Manager
• LMR and HTV Logos on the card
• "Dramatically increase the value of your property"
Nice to have
• Colour Scheme:
• Gloss black business card, with white and then
• Gold or Silver as the highlight colours.
• Incorporate a small amount of yellow only if possible to make it pop. If this really doesn’t work it doesn’t have to be used. Also l like the colour teal if that needs to be used as a contrast colour.
• Also like teal as a highlight colour.

```html
<!DOCTYPE html>
<html lang="en">
<head>
<meta charset="utf-8">
<title>DM Space Arranging Pty Ltd – Business Card</title>
<link rel="stylesheet" href="https://fonts.googleapis.com/css2?family=Great+Vibes&family=Tinos:wght@400&display=swap">
<style>
  :root {
    --stage: #e8e7e4;
    --card: #ffffff;
    --gloss-black: #0d0d0d;
    --ink: #222222;
    --silver: #9a9a9a;
    --mark-tint: #e4e4e4;
    --teal: #33b8a4;
    --gold-dark: #8a6a1c;
    --gold-light: #f3d67a;
    --band-text: #b5b5b5;
  }
  * { margin: 0; padding: 0; box-sizing: border-box; }
  html, body { width: 1200px; height: 852px; overflow: hidden; background: var(--stage); }
  .canvas { position: relative; width: 1200px; height: 852px; }

  .card {
    position: absolute;
    left: 280px;
    width: 640px;
    height: 365px;
    background: var(--card);
    border-radius: 14px;
    overflow: hidden;
    box-shadow: 0 6px 18px rgba(0,0,0,.18);
  }
  .card--front { top: 40px; }
  .card--back { top: 447px; }
  .card__bands { position: absolute; inset: 0; width: 100%; height: 100%; }

  .brand {
    position: absolute;
    display: flex;
    align-items: center;
    gap: 12px;
    font-family: "Tinos", "Times New Roman", serif;
    font-weight: 400;
    color: var(--ink);
    text-transform: uppercase;
    letter-spacing: 0.2em;
    white-space: nowrap;
  }
  .brand__dot {
    width: 34px; height: 34px; border-radius: 50%;
    background: var(--mark-tint);
    flex: none;
  }
  .card--front .brand { left: 70px; top: 150px; font-size: 19px; }
  .card--back .brand { left: 38px; top: 112px; font-size: 15px; }
  .card--back .brand__dot { width: 26px; height: 26px; }

  .identity {
    position: absolute;
    right: 40px;
    top: 26px;
    text-align: right;
    font-family: "Tinos", "Times New Roman", serif;
    color: var(--ink);
  }
  .identity__name {
    font-family: "Great Vibes", cursive;
    font-size: 38px;
    line-height: 1.1;
    margin-bottom: 2px;
  }
  .identity__role { font-size: 15px; line-height: 1.25; }

  .services {
    position: absolute;
    left: 40px;
    top: 176px;
    list-style: none;
    font-family: "Tinos", "Times New Roman", serif;
    font-size: 16px;
    line-height: 23px;
    color: var(--ink);
  }
  .services li::before {
    content: "»";
    color: var(--teal);
    margin-right: 9px;
  }

  .tagline {
    position: absolute;
    left: 38px;
    bottom: 24px;
    font-family: "Tinos", "Times New Roman", serif;
    font-size: 15px;
    color: var(--band-text);
  }
</style>
</head>
<body>
<main class="canvas">

  <section class="card card--front" aria-label="Business card front">
    <svg class="card__bands" viewBox="0 0 640 365" aria-hidden="true">
      <defs>
        <linearGradient id="gold-front" x1="0" y1="0" x2="1" y2="0">
          <stop offset="0" stop-color="var(--gold-dark)"/>
          <stop offset="0.45" stop-color="var(--gold-light)"/>
          <stop offset="1" stop-color="var(--gold-dark)"/>
        </linearGradient>
      </defs>
      <polygon points="0,332 150,365 0,365" fill="var(--gloss-black)"/>
      <polygon points="60,365 640,292 640,300 110,365" fill="url(#gold-front)"/>
    </svg>
    <div class="brand"><span class="brand__dot"></span>DM Space Arranging Pty Ltd</div>
  </section>

  <section class="card card--back" aria-label="Business card back">
    <svg class="card__bands" viewBox="0 0 640 365" aria-hidden="true">
      <defs>
        <linearGradient id="gold-back" x1="0" y1="0" x2="1" y2="0">
          <stop offset="0" stop-color="var(--gold-dark)"/>
          <stop offset="0.5" stop-color="var(--gold-light)"/>
          <stop offset="1" stop-color="var(--gold-dark)"/>
        </linearGradient>
        <linearGradient id="gloss" x1="0" y1="0" x2="0" y2="1">
          <stop offset="0" stop-color="#2a2a2a"/>
          <stop offset="1" stop-color="var(--gloss-black)"/>
        </linearGradient>
      </defs>
      <polygon points="0,306 640,250 640,365 0,365" fill="url(#gloss)"/>
      <polygon points="0,300 640,244 640,250 0,306" fill="url(#gold-back)"/>
    </svg>

    <div class="identity">
      <p class="identity__name">Marnie Tulloch</p>
      <p class="identity__role">B.Com LMR HTV</p>
      <p class="identity__role">Property Stylist &amp;</p>
      <p class="identity__role">Project Manager</p>
    </div>

    <div class="brand"><span class="brand__dot"></span>DM Space Arranging Pty Ltd</div>

    <ul class="services">
      <li>Staging Houses for Sale</li>
      <li>Minor Home Renovations</li>
      <li>Home Styling &amp; Project Management</li>
      <li>Re-Designing Living Spaces to Aid the Disabled</li>
    </ul>

    <p class="tagline">Property Styling &amp; Cosmetic Renovations</p>
  </section>

</main>
</body>
</html>
```